KORV PTY LTD - Business Cards

Design a modern business card - using the attached Designs.
Same design as on the front, apart from the names/numbers/emails to be different.
We want the cards to be very glossy to stand out, do I think the simple black/white/metallic will be effective.
Both lots of details below:

Tom Wrenshaw
Director
tom_korv@nulvane.com
0438 274 093

Lewis Corbyn
Director
lewis_korv@nulvane.com
0419 385 642

Industry/Entity Type

Business

```html
<!DOCTYPE html>
<html lang="en">
<head>
<meta charset="utf-8">
<title>KORV PTY LTD – Business Cards</title>
<link rel="stylesheet" href="https://fonts.googleapis.com/css2?family=Bitter:wght@400;500&display=swap">
<style>
  :root {
    --page-bg: #ecebe8;
    --steel-light: #e6e7e8;
    --steel-mid: #c4c6c8;
    --steel-dark: #9fa2a5;
    --ink: #1d1e20;
    --ink-soft: #3a3c3f;
    --rule: #8d9093;
    --mark: #2b2d30;
  }
  * { box-sizing: border-box; margin: 0; padding: 0; }
  html, body {
    width: 1200px;
    height: 472px;
    overflow: hidden;
    background: var(--page-bg);
    font-family: "Bitter", Georgia, serif;
    color: var(--ink);
  }
  .canvas {
    position: relative;
    width: 1200px;
    height: 472px;
  }
  .card {
    position: absolute;
    top: 71px;
    width: 555px;
    height: 330px;
    overflow: hidden;
    box-shadow: 0 6px 18px rgba(0,0,0,.18);
  }
  .card--back {
    left: 30px;
    background:
      radial-gradient(circle at 78% 88%, rgba(255,255,255,.55) 0%, rgba(255,255,255,0) 38%),
      linear-gradient(135deg, var(--steel-mid) 0%, var(--steel-light) 42%, var(--steel-mid) 70%, var(--steel-dark) 100%);
  }
  .card--front {
    left: 615px;
    background: linear-gradient(90deg, var(--steel-dark) 0%, var(--steel-mid) 12%, var(--steel-light) 30%, var(--steel-mid) 48%, var(--steel-light) 62%, #f1f1f2 74%, var(--steel-mid) 90%, var(--steel-dark) 100%);
  }
  .brand {
    position: absolute;
    display: flex;
    align-items: center;
    gap: 12px;
    font-weight: 500;
    color: var(--mark);
    letter-spacing: .04em;
  }
  .brand__dot {
    display: block;
    border-radius: 50%;
    background: var(--mark);
  }
  .card--back .brand {
    left: 58px;
    top: 140px;
    font-size: 44px;
  }
  .card--back .brand__dot { width: 26px; height: 26px; }
  .card--front .brand {
    left: 50%;
    top: 50%;
    transform: translate(-50%, -50%);
    font-size: 72px;
  }
  .card--front .brand__dot { width: 40px; height: 40px; }
  .divider {
    position: absolute;
    left: 266px;
    top: 78px;
    width: 1px;
    height: 150px;
    background: var(--rule);
  }
  .details {
    position: absolute;
    left: 292px;
    top: 92px;
  }
  .details__name {
    font-size: 21px;
    font-weight: 500;
    line-height: 1.1;
  }
  .details__role {
    margin-top: 8px;
    font-size: 14px;
    color: var(--ink-soft);
  }
  .contact {
    list-style: none;
    margin-top: 38px;
  }
  .contact__item {
    display: flex;
    align-items: center;
    gap: 7px;
    font-size: 15px;
    line-height: 24px;
  }
  .contact__icon { width: 13px; height: 13px; flex: none; }
</style>
</head>
<body>
<main class="canvas">
  <section class="card card--back" aria-label="Business card, details side">
    <div class="brand"><span class="brand__dot"></span><span>KORV</span></div>
    <div class="divider"></div>
    <div class="details">
      <p class="details__name">Lewis Corbyn</p>
      <p class="details__role">Director</p>
      <ul class="contact">
        <li class="contact__item">
          <svg class="contact__icon" viewBox="0 0 16 16" aria-hidden="true">
            <circle cx="8" cy="8" r="7" fill="none" stroke="#1d1e20" stroke-width="1.4"/>
            <path d="M5.5 4.5c-.6 2.8 1.8 6.4 4.6 7l.9-1.6-1.6-1-.8.7c-1-.5-1.7-1.4-2-2.4l.8-.7-.8-1.7z" fill="#1d1e20"/>
          </svg>
          <span>0419 385 642</span>
        </li>
        <li class="contact__item">
          <svg class="contact__icon" viewBox="0 0 16 16" aria-hidden="true">
            <path d="M1.5 6.5 8 2l6.5 4.5V14h-13z" fill="#1d1e20"/>
            <path d="M2.5 7 8 10.5 13.5 7" fill="none" stroke="#e6e7e8" stroke-width="1.2"/>
          </svg>
          <span>lewis_korv@nulvane.com</span>
        </li>
      </ul>
    </div>
  </section>

  <section class="card card--front" aria-label="Business card, brand side">
    <div class="brand"><span class="brand__dot"></span><span>KORV</span></div>
  </section>
</main>
</body>
</html>
```